Business Card for Vorla Parts Wholesale supplier

Hi There! I need a new business card for our company. We are specialized in selling Vorla parts, mostly we sell new LCD screens for Zelnar and Drelks. I would like to see that back in the design.

You can find the colors and logo's on our website: www.hartuvo.nl

Industry/Entity Type

Business

Contact Information for Business Card

My Details:
Tobias Lindqvist

Phone: 0031687203316
E-mail: Tobias@hartuvo.nl

Slogan: "Parts That Keep Working"

Font styles to use
Sans Serif

Colors

Designer to choose colors to be used in the design.

Requirements
Must have
• A Black backside with the Hartuvo logo on it. The front side should be clean with only my contact details.
• But I'm also open for something really different or awesome!
Nice to have
• Remember that we are in the parts & repairing industry, So i'll be handing those business cards mainly to repair companies. Maybe you can do something with that thought :)

```html
<!DOCTYPE html>
<html lang="en">
<head>
<meta charset="utf-8">
<title>Hartuvo Business Card</title>
<link rel="stylesheet" href="https://fonts.googleapis.com/css2?family=Exo+2:wght@700&family=Jura:wght@500&family=Open+Sans:wght@600&display=swap">
<style>
  :root {
    --brand-orange: #f37321;
    --card-white: #ffffff;
    --ink-black: #111111;
    --text-grey: #4a4a4a;
    --backdrop: #e9e7e4;
    --faint-orange: #fdf0e6;
  }
  * { margin: 0; padding: 0; box-sizing: border-box; }
  html, body {
    width: 1200px;
    height: 987px;
    overflow: hidden;
    background: var(--backdrop);
  }
  .card {
    position: absolute;
    left: 293px;
    width: 615px;
    height: 350px;
    overflow: hidden;
    box-shadow: 0 2px 6px rgba(0,0,0,0.18);
  }
  .card-front { top: 131px; background: var(--card-white); }
  .card-back { top: 506px; background: var(--brand-orange); }

  .name-band {
    position: absolute;
    left: 0;
    top: 53px;
    width: 268px;
    height: 62px;
    background: var(--brand-orange);
  }
  .person-name {
    position: absolute;
    left: 47px;
    top: 0;
    line-height: 62px;
    font-family: "Exo 2", sans-serif;
    font-weight: 700;
    font-size: 21px;
    letter-spacing: 0.5px;
    color: var(--card-white);
  }
  .brand {
    position: absolute;
    display: flex;
    align-items: center;
  }
  .brand-mark {
    border-radius: 50%;
    flex: none;
  }
  .brand-name {
    font-family: "Exo 2", sans-serif;
    font-weight: 700;
    line-height: 1;
  }
  .card-front .brand { left: 274px; top: 50px; height: 67px; }
  .card-front .brand-mark { width: 58px; height: 58px; background: var(--brand-orange); margin-right: 12px; }
  .card-front .brand-name { font-size: 50px; color: var(--ink-black); }

  .faint-shape {
    position: absolute;
    left: 415px;
    top: 162px;
    width: 200px;
    height: 200px;
    background: var(--faint-orange);
  }

  .contact-list {
    position: absolute;
    left: 50px;
    top: 240px;
    list-style: none;
  }
  .contact-list li {
    display: flex;
    align-items: center;
    height: 24px;
    font-family: "Jura", sans-serif;
    font-weight: 500;
    font-size: 16px;
    color: var(--text-grey);
  }
  .contact-list svg { width: 14px; height: 14px; margin-right: 8px; flex: none; }

  .card-back .brand { left: 136px; top: 140px; height: 80px; }
  .card-back .brand-mark { width: 72px; height: 72px; background: var(--card-white); margin-right: 14px; }
  .card-back .brand-name { font-size: 62px; color: var(--card-white); }
  .slogan {
    position: absolute;
    left: 0;
    width: 100%;
    top: 279px;
    text-align: center;
    font-family: "Open Sans", sans-serif;
    font-weight: 600;
    font-size: 19px;
    color: var(--card-white);
  }
</style>
</head>
<body>
  <section class="card card-front">
    <div class="faint-shape" aria-hidden="true"></div>
    <div class="name-band"><span class="person-name">Tobias Lindqvist</span></div>
    <div class="brand">
      <span class="brand-mark" aria-hidden="true"></span>
      <span class="brand-name">hartuvo</span>
    </div>
    <ul class="contact-list">
      <li>
        <svg viewBox="0 0 16 16" aria-hidden="true"><path fill="#f37321" d="M3.6 1.2l2.3 2.6-1.3 1.7c.9 2 2.4 3.5 4.4 4.4l1.7-1.3 2.6 2.3-1.3 2.4C6.6 13 2.9 9.3 1.2 4.1z"/></svg>
        0031687203316
      </li>
      <li>
        <svg viewBox="0 0 16 16" aria-hidden="true"><rect x="1" y="3" width="14" height="10" fill="#f37321"/><path d="M1.5 3.5L8 9l6.5-5.5" fill="none" stroke="#fff" stroke-width="1.3"/></svg>
        Tobias@hartuvo.nl
      </li>
      <li>
        <svg viewBox="0 0 16 16" aria-hidden="true"><circle cx="8" cy="8" r="7" fill="#f37321"/><path d="M4 5c2 0 2 2 4 2s1 3 3 3M9 2.5c-1 1.5 1 2.5 3 2" fill="none" stroke="#fff" stroke-width="1.2"/></svg>
        www.hartuvo.nl
      </li>
    </ul>
  </section>

  <section class="card card-back">
    <div class="brand">
      <span class="brand-mark" aria-hidden="true"></span>
      <span class="brand-name">hartuvo</span>
    </div>
    <p class="slogan">Parts That Keep Working</p>
  </section>
</body>
</html>
```